Business card design for Quorvel Engineering Tandem

We need a new business card design along with all the necessary to place an order. The company is Quorvel Engineering Tandem and we recently updated our logo.

```html
<!DOCTYPE html>
<html lang="en">
<head>
<meta charset="utf-8">
<title>Quorvel Engineering Tandem – Business Card</title>
<link href="https://fonts.googleapis.com/css2?family=Poppins:wght@400;500;600&display=swap" rel="stylesheet">
<style>
  :root{
    --backdrop:#3a3a3a;
    --card:#2e2e2f;
    --grey:#9a9a9a;
    --light:#d8d8d8;
    --yellow:#e3bd1f;
    --dark-band:#262627;
  }
  *{margin:0;padding:0;box-sizing:border-box}
  html,body{width:1200px;height:689px;overflow:hidden}
  body{background:var(--backdrop);font-family:"Poppins",sans-serif;position:relative}
  .card{position:absolute;top:195px;width:525px;height:300px;background:var(--card);border-radius:16px;overflow:hidden}
  .card-front{left:45px}
  .card-back{left:630px}

  .brand{display:flex;align-items:center;gap:14px;color:var(--grey);font-weight:600;letter-spacing:.05em;text-transform:uppercase;white-space:nowrap}
  .brand-mark{width:24px;height:24px;background:var(--grey);flex:none}
  .card-front .brand{position:absolute;left:0;right:0;top:0;bottom:0;justify-content:center;font-size:24px}
  .card-back .brand{position:absolute;left:36px;top:38px;font-size:21px}
  .card-back .brand-mark{background:var(--yellow);width:20px;height:20px}

  .contact-block{position:absolute;left:36px;top:128px;padding-left:22px}
  .accent-bar{position:absolute;left:0;top:4px;width:8px;height:46px;background:var(--yellow)}
  .person-name{color:var(--yellow);font-weight:600;font-size:22px;letter-spacing:.02em;line-height:1.1}
  .person-role{color:var(--light);font-size:12px;letter-spacing:.08em;margin-top:4px}
  .contact-list{list-style:none;margin-top:20px}
  .contact-list li{display:flex;align-items:center;gap:8px;color:var(--light);font-size:13px;line-height:1.45}
  .contact-list svg{width:12px;height:12px;flex:none}

  .address{position:absolute;right:34px;top:200px;text-align:right;color:var(--light);font-size:14px;line-height:1.5}

  .base-band{position:absolute;left:0;bottom:0;width:100%;height:18px}
</style>
</head>
<body>
  <section class="card card-front">
    <div class="brand"><span class="brand-mark"></span>Quorvel Engineering Tandem</div>
  </section>

  <section class="card card-back">
    <div class="brand"><span class="brand-mark"></span>Quorvel Engineering Tandem</div>

    <div class="contact-block">
      <span class="accent-bar"></span>
      <p class="person-name">MARCUS HALE</p>
      <p class="person-role">MANAGING DIRECTOR</p>
      <ul class="contact-list">
        <li><svg viewBox="0 0 24 24"><path fill="var(--yellow)" d="M6.6 10.8a15 15 0 006.6 6.6l2.2-2.2c.3-.3.7-.4 1-.2 1.1.4 2.3.6 3.6.6.6 0 1 .4 1 1V20c0 .6-.4 1-1 1A17 17 0 013 4c0-.6.4-1 1-1h3.5c.6 0 1 .4 1 1 0 1.3.2 2.5.6 3.6.1.3 0 .7-.2 1z"/></svg>044-987 654 321</li>
        <li><svg viewBox="0 0 24 24"><rect x="2" y="5" width="20" height="14" fill="var(--yellow)"/><path d="M2 5l10 8 10-8" stroke="var(--card)" stroke-width="2" fill="none"/></svg>hello@quorveltandem.com</li>
        <li><svg viewBox="0 0 24 24" fill="none" stroke="var(--yellow)" stroke-width="2"><circle cx="12" cy="12" r="9"/><path d="M3 12h18M12 3c3 3 3 15 0 18M12 3c-3 3-3 15 0 18"/></svg>www.quorveltandem.com</li>
      </ul>
    </div>

    <p class="address">48 Kiln Road,<br>Northfield, 204518</p>

    <svg class="base-band" viewBox="0 0 525 18" preserveAspectRatio="none">
      <rect x="0" y="0" width="525" height="18" fill="var(--grey)"/>
      <polygon points="0,0 330,0 318,18 0,18" fill="var(--yellow)"/>
      <polygon points="330,0 346,0 334,18 318,18" fill="var(--dark-band)"/>
    </svg>
  </section>
</body>
</html>
```